Senior sex novelty store providing a private method for acquiring the products and knowledge

Our business supplies novelty sex products and services, specializing in the 50+ demographic. Products include sex products for individuals and couples. Services include webinars and teleseminars that address various sex and relationship issues. We are dedicated to providing discreet delivery of products and knowledge to people over 50 entering a new phase of life, facing new challenges. Our entire process from site through shipping is kept private to allow our customers the freedom to shop and learn in the privacy of their own home.

Target Market(s)

Seniors over 50 years old

Industry/Entity Type

Store

Number of Pages Required

1 page

Font styles to use
Serif

Requirements
Must have
• place for business description with a private look
Should not have
• anything sleazy

```html
<!DOCTYPE html>
<html lang="en">
<head>
<meta charset="utf-8">
<title>Quiet Season — Private store</title>
<link href="https://fonts.googleapis.com/css2?family=Ubuntu:wght@300;400;500;700&display=swap" rel="stylesheet">
<style>
:root{
  --red:#d13c33;
  --red-dark:#b8322a;
  --ink:#3a3a3a;
  --muted:#6a6a6a;
  --topbar:#1f1f24;
  --night:#2b2a31;
  --night-deep:#1b1b1f;
  --line:#d9d9d9;
  --white:#ffffff;
}
*{box-sizing:border-box;margin:0;padding:0}
html,body{width:1200px;height:3108px;overflow:hidden}
body{font-family:'Ubuntu',sans-serif;color:var(--ink);background:var(--white);position:relative}
.abs{position:absolute}
a{color:inherit;text-decoration:none}

.topbar{top:0;left:0;width:1200px;height:49px;background:var(--topbar);color:var(--white);font-size:14px}
.topbar .welcome{left:96px;top:16px}
.topbar .account{left:806px;top:16px;font-size:13px}
.topbar .cart{left:920px;top:16px;font-size:13px}
.topbar .search{left:1016px;top:0;width:184px;height:49px;background:var(--red);display:flex;align-items:center;justify-content:center}

.header{top:49px;left:0;width:1200px;height:117px}
.brand{left:96px;top:40px;display:flex;align-items:center;gap:12px;font-size:28px;font-weight:700;color:var(--red)}
.brand .mark{width:30px;height:30px;background:var(--red);border-radius:50%}
.nav{right:96px;top:56px;display:flex;gap:40px;font-size:15px;letter-spacing:.5px}
.nav .active{color:var(--red)}

.hero{top:166px;left:0;width:1200px;height:464px;background:linear-gradient(100deg,#6d5147 0%,#b48d7c 30%,#d9c3b4 55%,#e8dcd2 75%,#cdbbb0 100%)}
.hero-tag{background:var(--red);color:var(--white);text-align:center}
.hero .kicker{left:705px;top:142px;width:301px;height:52px;font-size:34px;line-height:52px;font-weight:300}
.hero .title{left:609px;top:205px;width:495px;height:83px;font-size:50px;line-height:83px;font-weight:400}
.hero .cta{left:759px;top:295px;width:200px;height:52px;font-size:22px;line-height:52px;clip-path:polygon(0 0,100% 0,94% 100%,6% 100%)}

.section-title{border:2px solid var(--ink);text-align:center;font-size:26px;letter-spacing:1px;display:flex;align-items:center;justify-content:center}
.section-title.light{border-color:var(--white);color:var(--white)}

.products-title{left:498px;top:700px;width:202px;height:54px}
.products-intro{left:96px;top:793px;width:1008px;font-size:15px;line-height:26px;text-align:center;color:var(--muted)}
.product{top:907px;width:321px}
.product .photo{height:213px}
.product h3{margin-top:30px;text-align:center;font-weight:400;font-size:22px;letter-spacing:.5px}
.underline{width:52px;height:3px;background:var(--red);margin:10px auto 0}
.product p{margin:16px auto 0;width:230px;text-align:center;font-size:12px;line-height:16px;color:var(--muted)}
.product .actions{display:flex;justify-content:center;margin-top:22px}
.btn-more{width:112px;height:39px;background:#ebebeb;font-size:12px;line-height:39px;text-align:center;color:var(--muted)}
.btn-cart{width:56px;height:39px;background:var(--red);display:flex;align-items:center;justify-content:center}
.view-more{left:0;top:1438px;width:1200px;text-align:center;font-size:26px;letter-spacing:.5px}

.blog{top:1550px;left:0;width:1200px;height:635px;background:linear-gradient(120deg,#25242a 0%,#3a3438 40%,#4b4042 60%,#2a292f 100%)}
.blog-title{left:453px;top:85px;width:293px;height:55px}
.post{width:300px;color:var(--white)}
.post .head{display:flex;align-items:center;gap:18px}
.post .num{width:47px;height:47px;background:var(--white);color:var(--night);font-weight:700;font-size:32px;display:flex;align-items:center;justify-content:center}
.post h4{font-weight:400;font-size:21px}
.post .bar{width:52px;height:3px;background:var(--red);margin:4px 0 0 65px}
.post p{margin-top:18px;font-size:14px;line-height:20px;opacity:.95}
.post .read{display:block;margin-top:20px;font-weight:700;font-size:15px;letter-spacing:.5px}

.rel-title{left:440px;top:2255px;width:322px;height:57px}
.rel-photo{left:96px;top:2377px;width:285px;height:215px;background:linear-gradient(135deg,#c79b86,#8a5f4e 55%,#e7ddd4)}
.rel-head{left:422px;top:2414px;font-size:18px;letter-spacing:.3px}
.rel-head .underline{margin:8px 0 0}
.rel-text{left:422px;top:2458px;width:620px;font-size:16px;line-height:26px;color:var(--muted)}
.arrows{left:1008px;top:2374px;display:flex;gap:4px}
.arrows span{width:46px;height:44px;background:#d3d3d3;display:flex;align-items:center;justify-content:center}

.info{top:2654px;left:0;width:1200px;height:363px;background:linear-gradient(120deg,#2a2930,#3b3539 50%,#25242a)}
.info-col{top:0;width:332px;height:314px;background:rgba(30,30,34,.55);color:var(--white);text-align:center}
.info-col h5{height:98px;background:var(--red);font-weight:400;font-size:26px;line-height:98px}
.info-col.mid h5{background:var(--red-dark)}
.info-col .dash{width:40px;height:2px;background:var(--white);margin:30px auto 0}
.info-col p{width:250px;margin:16px auto 0;font-size:13px;line-height:19px}
.info-col .outline{display:inline-block;margin-top:32px;border:2px solid var(--white);padding:8px 22px;font-size:14px}
.signup{display:flex;justify-content:center;margin-top:26px}
.signup .field{width:184px;height:38px;border:2px solid var(--white)}
.signup .send{width:82px;height:38px;background:#d9d9d9;color:var(--night);font-size:14px;line-height:38px}

.footer{top:3017px;left:0;width:1200px;height:91px;background:var(--night-deep);color:var(--white);font-size:14px}
.footer .copy{left:96px;top:36px}
.footer .links{left:486px;top:36px;display:flex;gap:16px}
.footer .social{left:920px;top:30px;display:flex;gap:8px}
.footer .social span{width:24px;height:24px;background:var(--red);border-radius:3px}
</style>
</head>
<body>

<div class="abs topbar">
  <span class="abs welcome">Welcome to our site visitors</span>
  <span class="abs account">LOGIN | SIGNUP</span>
  <span class="abs cart">
    <svg width="14" height="12" viewBox="0 0 14 12" style="vertical-align:-1px"><path d="M0 1h3l2 7h7l2-5H4" fill="none" stroke="#d13c33" stroke-width="1.6"/><circle cx="6" cy="10.5" r="1.2" fill="#d13c33"/><circle cx="11" cy="10.5" r="1.2" fill="#d13c33"/></svg>
    &nbsp;$ 100.00</span>
  <span class="abs search"><svg width="16" height="16" viewBox="0 0 16 16"><circle cx="6.5" cy="6.5" r="5" fill="none" stroke="#fff" stroke-width="2"/><path d="M10 10l5 5" stroke="#fff" stroke-width="2"/></svg></span>
</div>

<header class="abs header">
  <a class="abs brand" href="#"><span class="mark"></span>QUIETSEASON</a>
  <nav class="abs nav">
    <a class="active" href="#">HOME</a><a href="#">PRODUCTS</a><a href="#">SERVICES</a><a href="#">SHIPPING</a><a href="#">PAYMENT</a><a href="#">CONTACT</a>
  </nav>
</header>

<section class="abs hero" role="img" aria-label="Soft-lit portrait of a woman resting on pale bedding">
  <div class="abs hero-tag kicker">DOLOREMUE</div>
  <div class="abs hero-tag title">AUT ASPERNATUR</div>
  <a class="abs hero-tag cta" href="#">READ MORE</a>
</section>

<h2 class="abs section-title products-title">PRODUCTS</h2>
<p class="abs products-intro">Lorem ipsum dolor sit amet rem eos illo omnis aut aperiam ab ipsam ipsa odit aut aperiam aut aspernatur veritatis unde sed enim accusantium laudantium sunt perspiciatis ipsam sed doloremque ipsam dolores totam unde aut illo aut veritatis explicabo dicta quia dicta veritatis dicta sunt quasi eaque rem</p>

<article class="abs product" style="left:96px">
  <div class="photo" role="img" aria-label="Textured pale massage glove" style="background:linear-gradient(135deg,#f3ebe6,#dcc2b6 50%,#f6f1ee)"></div>
  <h3>NEW ARRIVALS</h3><div class="underline"></div>
  <p>Lorem ipsum dolar sit amet voluptatem fugit illo omnisa explicabo nemo rem ipsam quas dolores voluptatem doloremque perspiciatis</p>
  <div class="actions"><a class="btn-more" href="#">LEARN MORE</a><a class="btn-cart" href="#"><svg width="20" height="16" viewBox="0 0 14 12"><path d="M0 1h3l2 7h7l2-5H4z" fill="#fff"/><circle cx="6" cy="10.5" r="1.3" fill="#fff"/><circle cx="11" cy="10.5" r="1.3" fill="#fff"/></svg></a></div>
</article>

<article class="abs product" style="left:438px">
  <div class="photo" role="img" aria-label="Pink personal product held in hand" style="background:linear-gradient(135deg,#f4e9e2,#e78cc0 50%,#f5eee8)"></div>
  <h3>FOR INDIVIDUALS</h3><div class="underline"></div>
  <p>Lorem ipsum dolar sit amet voluptatem fugit illo omnisa explicabo nemo rem ipsam quas dolores voluptatem doloremque perspiciatis</p>
  <div class="actions"><a class="btn-more" href="#">LEARN MORE</a><a class="btn-cart" href="#"><svg width="20" height="16" viewBox="0 0 14 12"><path d="M0 1h3l2 7h7l2-5H4z" fill="#fff"/><circle cx="6" cy="10.5" r="1.3" fill="#fff"/><circle cx="11" cy="10.5" r="1.3" fill="#fff"/></svg></a></div>
</article>

<article class="abs product" style="left:783px">
  <div class="photo" role="img" aria-label="Pair of soft pink plush cuffs" style="background:linear-gradient(135deg,#eceef4,#e07aa6 50%,#eef0f5)"></div>
  <h3>FOR COUPLES</h3><div class="underline"></div>
  <p>Lorem ipsum dolar sit amet voluptatem fugit illo omnisa explicabo nemo rem ipsam quas dolores voluptatem doloremque perspiciatis</p>
  <div class="actions"><a class="btn-more" href="#">LEARN MORE</a><a class="btn-cart" href="#"><svg width="20" height="16" viewBox="0 0 14 12"><path d="M0 1h3l2 7h7l2-5H4z" fill="#fff"/><circle cx="6" cy="10.5" r="1.3" fill="#fff"/><circle cx="11" cy="10.5" r="1.3" fill="#fff"/></svg></a></div>
</article>

<a class="abs view-more" href="#">VIEW MORE PRODUCTS</a>

<section class="abs blog" role="img" aria-label="Dim, warm-toned backdrop of a couple embracing">
  <h2 class="abs section-title light blog-title">NEWS FROM BLOG</h2>

  <article class="abs post" style="left:96px;top:205px"><div class="head"><span class="num">1</span><h4>AMET VOLUPTATEM</h4></div><div class="bar"></div><p>Lorem ipsum dolor sit amet rem illo omnis aperiam ab ipsam ipsa odit aut aperiam aspernatur veritatis unde enim accusantium laudantium sunt veritatis</p><a class="read" href="#">READ MORE</a></article>
  <article class="abs post" style="left:451px;top:205px"><div class="head"><span class="num">2</span><h4>AMET VOLUPTATEM</h4></div><div class="bar"></div><p>Lorem ipsum dolor sit amet rem illo omnis aperiam ab ipsam ipsa odit aut aperiam aspernatur veritatis unde enim accusantium laudantium sunt</p><a class="read" href="#">READ MORE</a></article>
  <article class="abs post" style="left:806px;top:205px"><div class="head"><span class="num">3</span><h4>AMET VOLUPTATEM</h4></div><div class="bar"></div><p>Lorem ipsum dolor sit amet rem illo omnis aperiam ab ipsam ipsa odit aut aperiam aspernatur veritatis unde enim accusantium laudantium sunt</p><a class="read" href="#">READ MORE</a></article>

  <article class="abs post" style="left:96px;top:412px"><div class="head"><span class="num">4</span><h4>AMET VOLUPTATEM</h4></div><div class="bar"></div><p>Lorem ipsum dolor sit amet rem illo omnis aperiam ab ipsam ipsa odit aut aperiam aspernatur veritatis unde enim accusantium laudantium sunt</p><a class="read" href="#">READ MORE</a></article>
  <article class="abs post" style="left:451px;top:412px"><div class="head"><span class="num">5</span><h4>AMET VOLUPTATEM</h4></div><div class="bar"></div><p>Lorem ipsum dolor sit amet rem illo omnis aperiam ab ipsam ipsa odit aut aperiam aspernatur veritatis unde enim accusantium laudantium sunt</p><a class="read" href="#">READ MORE</a></article>
  <article class="abs post" style="left:806px;top:412px"><div class="head"><span class="num">6</span><h4>AMET VOLUPTATEM</h4></div><div class="bar"></div><p>Lorem ipsum dolor sit amet rem illo omnis aperiam ab ipsam ipsa odit aut aperiam aspernatur veritatis unde enim accusantium laudantium sunt</p><a class="read" href="#">READ MORE</a></article>
</section>

<h2 class="abs section-title rel-title">RELATIONSHIP ISSUES</h2>
<div class="abs arrows">
  <span><svg width="14" height="22" viewBox="0 0 14 22"><path d="M12 2L3 11l9 9" fill="none" stroke="#fff" stroke-width="2.5"/></svg></span>
  <span><svg width="14" height="22" viewBox="0 0 14 22"><path d="M2 2l9 9-9 9" fill="none" stroke="#fff" stroke-width="2.5"/></svg></span>
</div>
<div class="abs rel-photo" role="img" aria-label="Couple sharing a tender moment in bed"></div>
<div class="abs rel-head">OMNIS AUT APERIAM AB IPSAM IPSA ODIT AUT APERIAM AUT<div class="underline"></div></div>
<p class="abs rel-text">Lorem ipsum dolor sit amet rem eos illo omnis aut aperiam ab ipsam ipsa odit aut aperiam aspernatur veritatis unde, sed enim accusantium laudantium sunt perspiciatis ipsam sed doloremque ....</p>

<section class="abs info">
  <div class="abs info-col" style="left:96px">
    <h5>ABOUT US</h5><div class="dash"></div>
    <p>Lorem ipsum dolor amet omnis aperi ipsam ipsa odit aut aperiam aspernatur veritatis unde enim accusantium</p>
    <a class="outline" href="#">READ MORE</a>
  </div>
  <div class="abs info-col mid" style="left:433px">
    <h5>OUR STORES</h5><div class="dash"></div>
    <p>Lorem ipsum dolor sit amet omnis ipsam ipsa odit aut aperiam aspernatur veritatis unde enim accusantium</p>
    <a class="outline" href="#">FIND ON MAP</a>
  </div>
  <div class="abs info-col" style="left:770px">
    <h5>NEWSLETTER</h5><div class="dash"></div>
    <p>Lorem ipsum dolor sit amet omnis aperiam</p>
    <div class="signup"><span class="field"></span><span class="send">SEND</span></div>
    <p>ab ipsam ipsa odit aut aperiam aspernatur veritatis unde accusantium laudantium</p>
  </div>
</section>

<footer class="abs footer">
  <span class="abs copy">© 2015 <b>QUIET SEASON</b>. All rights reserved</span>
  <nav class="abs links"><a href="#">About us</a><a href="#">Term and use</a><a href="#">Privacy policy</a><a href="#">Contact us</a></nav>
  <div class="abs social" aria-label="Social links"><span></span><span></span><span></span><span></span><span></span></div>
</footer>

</body>
</html>
```